Home Health Company Needs a Corporate Identity Package

We need a corporate identity package (see what it should include below) for a home health care company. The design should be professional, uncluttered, simple and created in Publisher (so that we can edit the design in the future, if necessary. )
We need the following created:
-Presentation folder
-Business card template (color, double sided)
-Letterhead
-Stationary
-postcard sized marketing piece (5.5" x 8.5", color, double sided)

Target Market(s)

We are in the business of supplying personal care aids for in home care. Our services are directed towards older, retired individuals with some disability or illness. However, we will be marketing to the children or relatives of our in home clients. We want our logo to emphasize our reliability and personalized services.

Industry/Entity Type

Home Health Care

Requirements
Must have
• The design should be professional, uncluttered, simple and created in Publisher (so that we can edit the design in the future, if necessary. )

```html
<!DOCTYPE html>
<html lang="en">
<head>
<meta charset="utf-8">
<title>Alderwell Home Care – Letterhead</title>
<link rel="stylesheet" href="https://fonts.googleapis.com/css2?family=Open+Sans:wght@400;700&display=swap">
<style>
  :root {
    --backdrop: #e9eaec;
    --paper: #ffffff;
    --brand-blue: #5bc2ec;
    --brand-grey: #636368;
    --ink: #6d6e72;
    --watermark: #f1f1f2;
  }
  * { box-sizing: border-box; margin: 0; padding: 0; }
  html, body {
    width: 1200px;
    height: 936px;
    overflow: hidden;
    background: var(--backdrop);
    font-family: "Open Sans", Arial, sans-serif;
  }
  .letterhead {
    position: absolute;
    left: 300px;
    top: 44px;
    width: 600px;
    height: 848px;
    background: var(--paper);
    box-shadow: 0 2px 10px rgba(0,0,0,0.12);
    overflow: hidden;
  }
  .brand {
    position: absolute;
    left: 40px;
    top: 44px;
    display: flex;
    align-items: center;
    gap: 10px;
  }
  .brand-dot {
    width: 30px;
    height: 30px;
    border-radius: 50%;
    background: var(--brand-blue);
  }
  .brand-name {
    font-weight: 700;
    font-size: 24px;
    line-height: 1.05;
    color: var(--brand-blue);
    letter-spacing: -0.3px;
  }
  .contact {
    position: absolute;
    right: 40px;
    top: 40px;
    list-style: none;
    font-size: 9px;
    line-height: 1.35;
    color: var(--ink);
  }
  .contact li {
    display: flex;
    align-items: flex-start;
    gap: 5px;
    margin-bottom: 2px;
  }
  .contact-icon {
    flex: none;
    width: 10px;
    height: 10px;
    margin-top: 1px;
  }
  .watermark {
    position: absolute;
    left: 150px;
    top: 260px;
    width: 300px;
    height: 300px;
    border-radius: 50%;
    background: var(--watermark);
  }
  .footer-band {
    position: absolute;
    left: 0;
    bottom: 0;
    width: 100%;
    height: 22px;
    display: flex;
    gap: 3px;
  }
  .footer-band .band-blue { flex: 0 0 61%; background: var(--brand-blue); }
  .footer-band .band-grey { flex: 1; background: var(--brand-grey); }
</style>
</head>
<body>
  <main class="letterhead">
    <header class="brand">
      <span class="brand-dot"></span>
      <span class="brand-name">Alderwell<br>Home Care</span>
    </header>

    <ul class="contact">
      <li>
        <svg class="contact-icon" viewBox="0 0 10 10"><circle cx="5" cy="5" r="5" fill="#5bc2ec"/><path d="M3.2 2.6l1 .9-.5.8a3 3 0 0 0 1.9 1.9l.8-.5.9 1-.7.7C4.6 7.3 2.7 5.4 2.6 3.3z" fill="#fff"/></svg>
        <span>555-555-555</span>
      </li>
      <li>
        <svg class="contact-icon" viewBox="0 0 10 10"><circle cx="5" cy="5" r="5" fill="#5bc2ec"/><rect x="2.6" y="3.3" width="4.8" height="3.4" fill="none" stroke="#fff" stroke-width=".7"/><path d="M2.6 3.3L5 5.3l2.4-2" fill="none" stroke="#fff" stroke-width=".7"/></svg>
        <span>info@website.com</span>
      </li>
      <li>
        <svg class="contact-icon" viewBox="0 0 10 10"><circle cx="5" cy="5" r="5" fill="#5bc2ec"/><circle cx="5" cy="5" r="2.5" fill="none" stroke="#fff" stroke-width=".6"/><path d="M2.5 5h5M5 2.5c-1.2 1.4-1.2 3.6 0 5M5 2.5c1.2 1.4 1.2 3.6 0 5" fill="none" stroke="#fff" stroke-width=".5"/></svg>
        <span>www.website.com<br>street name, city name,<br>state zip code</span>
      </li>
    </ul>

    <div class="watermark" aria-hidden="true"></div>

    <footer class="footer-band" aria-hidden="true">
      <span class="band-blue"></span>
      <span class="band-grey"></span>
    </footer>
  </main>
</body>
</html>
```